Automotive eCommerce Business looking for a business card design

Looking for a clean and simple business card design. Our company name is "Brindle Auto" and we are a company specializing in the ecommerce sales of automotive parts, specifically for pick up trucks and large SUVs. Our company colours are red, black, and white.

Feel free to use the logo provided or create a new logo that you seem fit. Looking forward to your creative ideas!

Industry/Entity Type

Automotive

Contact Information for Business Card

We were thinking of a possibly two-sided design featuring just the logo and company name on one side, and personal information on the other side. Single sided designs will be considered as well.

Font styles to use
Serif
Sans Serif
Decorative

Colors
ec1f27
ffffff
000000

Requirements
Must have
• Space for employee's name, title, phone number and email address, along with the company address and website somewhere.

```html
<!DOCTYPE html>
<html lang="en">
<head>
<meta charset="UTF-8">
<title>Brindle Auto Ltd. – Business Card</title>
<link rel="stylesheet" href="https://fonts.googleapis.com/css2?family=Open+Sans:wght@400;600;700;800&display=swap">
<style>
  :root {
    --brand-red: #ec1f27;
    --card-black: #231f20;
    --ink-white: #ffffff;
    --stage: #d7d9dc;
  }
  * { margin: 0; padding: 0; box-sizing: border-box; }
  html, body {
    width: 1200px;
    height: 1200px;
    overflow: hidden;
  }
  body {
    background: var(--stage);
    font-family: "Open Sans", Arial, sans-serif;
    color: var(--ink-white);
    position: relative;
  }
  .card {
    position: absolute;
    left: 150px;
    width: 900px;
    height: 515px;
    background: var(--card-black);
    border-radius: 30px;
  }
  .card--front { top: 60px; }
  .card--back  { top: 625px; }

  /* Front side */
  .front-brand {
    position: absolute;
    inset: 0;
    display: flex;
    align-items: center;
    justify-content: center;
    gap: 30px;
  }
  .brand-square {
    width: 96px;
    height: 96px;
    background: var(--brand-red);
    border-radius: 14px;
  }
  .brand-name {
    font-weight: 700;
    font-size: 56px;
    letter-spacing: 1px;
    color: var(--ink-white);
    text-transform: uppercase;
  }

  /* Back side */
  .back-brand {
    position: absolute;
    left: 260px;
    top: 60px;
    display: flex;
    align-items: center;
    gap: 16px;
  }
  .back-brand .brand-square {
    width: 56px;
    height: 56px;
    border-radius: 9px;
  }
  .back-brand .brand-name {
    font-size: 30px;
  }
  .address {
    position: absolute;
    left: 80px;
    top: 200px;
    display: flex;
    gap: 12px;
    font-size: 21px;
    line-height: 1.3;
  }
  .address svg { flex: none; margin-top: 2px; }
  .person {
    position: absolute;
    right: 70px;
    top: 210px;
    text-align: right;
  }
  .person-name {
    color: var(--brand-red);
    font-weight: 700;
    font-size: 34px;
    text-transform: uppercase;
    letter-spacing: 0.5px;
  }
  .person-title {
    font-size: 22px;
    margin-top: 2px;
  }
  .contacts {
    position: absolute;
    left: 330px;
    top: 360px;
    list-style: none;
    font-size: 22px;
    line-height: 1.4;
  }
  .contacts li {
    display: flex;
    align-items: center;
    gap: 12px;
  }
  .contacts svg { flex: none; }
</style>
</head>
<body>

  <section class="card card--front" aria-label="Business card front">
    <div class="front-brand">
      <span class="brand-square"></span>
      <span class="brand-name">Brindle Auto Ltd.</span>
    </div>
  </section>

  <section class="card card--back" aria-label="Business card back">
    <div class="back-brand">
      <span class="brand-square"></span>
      <span class="brand-name">Brindle Auto</span>
    </div>

    <div class="address">
      <svg width="22" height="30" viewBox="0 0 22 30" aria-hidden="true">
        <path d="M11 1C5.5 1 1 5.3 1 10.7 1 18 11 29 11 29s10-11 10-18.3C21 5.3 16.5 1 11 1z" fill="var(--brand-red)"/>
        <circle cx="11" cy="10.5" r="4" fill="var(--card-black)"/>
      </svg>
      <p>1480 Ferris Ave<br>Harlow, LA 70912</p>
    </div>

    <div class="person">
      <p class="person-name">Marcus Dalton</p>
      <p class="person-title">Managing Director</p>
    </div>

    <ul class="contacts">
      <li>
        <svg width="20" height="20" viewBox="0 0 24 24" aria-hidden="true">
          <path d="M6.6 10.8a15.1 15.1 0 0 0 6.6 6.6l2.2-2.2c.3-.3.7-.4 1-.2 1.1.4 2.3.6 3.6.6.6 0 1 .4 1 1V20c0 .6-.4 1-1 1C10.6 21 3 13.4 3 4c0-.6.4-1 1-1h3.5c.6 0 1 .4 1 1 0 1.3.2 2.5.6 3.6.1.3 0 .7-.2 1l-2.3 2.2z" fill="var(--brand-red)"/>
        </svg>
        <span>555 204 7781</span>
      </li>
      <li>
        <svg width="20" height="20" viewBox="0 0 24 24" aria-hidden="true">
          <rect x="2" y="5" width="20" height="14" rx="2" fill="var(--brand-red)"/>
          <path d="M3 6l9 7 9-7" fill="none" stroke="var(--card-black)" stroke-width="1.8"/>
        </svg>
        <span>marcus@brindleautoltd.com</span>
      </li>
      <li>
        <svg width="20" height="20" viewBox="0 0 24 24" aria-hidden="true">
          <circle cx="12" cy="12" r="10" fill="var(--brand-red)"/>
          <path d="M2 12h20M12 2c3 3 3 17 0 20M12 2c-3 3-3 17 0 20" fill="none" stroke="var(--card-black)" stroke-width="1.5"/>
        </svg>
        <span>www.brindleautoltd.com</span>
      </li>
    </ul>
  </section>

</body>
</html>
```